The Doctor Velmora Hour Web Graphics

Hi! We have a Wellness Show
I need several different size graphics with the same content:
Facebook Cover Photo- no button
FB- 1200x628
Instagram 800x800- no button
Television 1920x1080- no button
Web Banner 200 x 800
Web Ad- 1200x 300
.psd files- some will have the button and some won't

Copy:
The All New Dr. Velmora Hour (logo) airing weekly in over 100 new markets in the US!

Button:
Click Here to Learn Where YOU Can Watch!

Photo:
Either Dr. Velmora in LabCoat or LARGE AUDIENCE SHOT-
These can be found here: https://files.quorbix.example/share/7Kp2RtXw9LmQ4vZ8

Here are some backgrounds: https://files.quorbix.example/share/3Hd6YsNc1BfJ5gT0
Here are some photos: https://files.quorbix.example/share/7Kp2RtXw9LmQ4vZ8

```html
<!DOCTYPE html>
<html lang="en">
<head>
<meta charset="utf-8">
<title>The Doctor Velmora Hour – Web Graphics</title>
<link href="https://fonts.googleapis.com/css2?family=Oswald:wght@300;400;500&family=Open+Sans:wght@400&display=swap" rel="stylesheet">
<style>
  :root {
    --board: #e6e6e6;
    --green-top: #7aa24a;
    --green-deep: #5f8a43;
    --navy: #1a3a92;
    --slate-a: #3e5a78;
    --slate-b: #37478a;
    --white: #ffffff;
    --label: #111111;
    --button-text: #1f3fa0;
  }
  * { margin: 0; padding: 0; box-sizing: border-box; }
  html, body { width: 1200px; height: 1200px; overflow: hidden; background: var(--board); }
  .board { position: relative; width: 1200px; height: 1200px; }

  .banner { position: absolute; overflow: hidden; background: var(--white); }
  .band-top { position: absolute; left: 0; right: 0; top: 0;
    background: linear-gradient(100deg, var(--green-top), var(--green-deep) 70%, #6f9a55); }
  .band-mid { position: absolute; left: 0; right: 0;
    background: linear-gradient(90deg, #7e9c6e 0%, #c9d6c0 22%, var(--white) 40%); }
  .band-bottom { position: absolute; left: 0; right: 0; bottom: 0;
    background: linear-gradient(160deg, var(--slate-a), #48608a 50%, var(--slate-b)); }
  .band-bottom::after { content: ""; position: absolute; inset: 0;
    background: radial-gradient(ellipse at 70% 120%, rgba(30,40,110,.55), transparent 60%); }

  .portrait { position: absolute; left: 0; bottom: 0;
    background: linear-gradient(180deg, #d9dfd6 0%, #eef0ec 45%, #f7f7f5 100%);
    -webkit-mask-image: linear-gradient(90deg, #000 75%, transparent);
    mask-image: linear-gradient(90deg, #000 75%, transparent); }

  .kicker { position: absolute; display: flex; align-items: center; gap: .7em;
    font-family: "Oswald", sans-serif; font-weight: 500; color: var(--white);
    letter-spacing: .08em; white-space: nowrap; transform: translateX(-50%); }
  .kicker .rule { display: block; height: 2px; background: var(--white); }

  .show-name { position: absolute; display: flex; align-items: center; gap: .35em;
    transform: translate(-50%, -50%); white-space: nowrap;
    font-family: "Oswald", sans-serif; font-weight: 400; color: var(--navy); line-height: 1; }
  .show-name .dot { display: block; width: .5em; height: .5em; border-radius: 50%; background: var(--navy); }

  .tagline { position: absolute; font-family: "Oswald", sans-serif; font-weight: 400;
    color: var(--white); white-space: nowrap; z-index: 1; }

  .cta { position: absolute; z-index: 1; display: flex; align-items: center; justify-content: center;
    font-family: "Oswald", sans-serif; font-weight: 400; color: var(--button-text);
    background: linear-gradient(180deg, #ffffff, #e4e6ec); border-radius: 5px;
    box-shadow: 0 3px 5px rgba(0,0,0,.35); letter-spacing: .02em; }

  .caption { position: absolute; font-family: "Open Sans", sans-serif; font-weight: 400;
    color: var(--label); font-size: 37px; line-height: 1; }

  /* cover */
  .cover { left: 66px; top: 117px; width: 1066px; height: 458px; }
  .cover .band-top { height: 108px; }
  .cover .band-mid { top: 108px; height: 244px; }
  .cover .band-bottom { height: 106px; }
  .cover .portrait { width: 320px; height: 458px; }
  .cover .kicker { left: 674px; top: 40px; font-size: 40px; }
  .cover .kicker .rule { width: 168px; }
  .cover .show-name { left: 674px; top: 230px; font-size: 72px; }
  .cover .tagline { left: 340px; top: 372px; font-size: 37px; }

  /* feed post */
  .feed { left: 66px; top: 666px; width: 682px; height: 357px; }
  .feed .band-top { height: 77px; }
  .feed .band-mid { top: 77px; height: 143px; }
  .feed .band-bottom { height: 137px; }
  .feed .portrait { width: 220px; height: 357px; }
  .feed .kicker { left: 435px; top: 30px; font-size: 24px; }
  .feed .kicker .rule { width: 100px; }
  .feed .show-name { left: 435px; top: 150px; font-size: 44px; }
  .feed .tagline { left: 235px; top: 234px; font-size: 23px; }
  .feed .cta { left: 278px; top: 283px; width: 330px; height: 38px; font-size: 19px; }

  /* square */
  .square { left: 777px; top: 666px; width: 357px; height: 357px; }
  .square .band-top { height: 92px; }
  .square .band-mid { top: 92px; height: 113px; }
  .square .band-bottom { height: 152px; }
  .square .portrait { width: 140px; height: 240px; }
  .square .kicker { left: 178px; top: 38px; font-size: 28px; }
  .square .kicker .rule { width: 66px; }
  .square .show-name { left: 226px; top: 150px; font-size: 30px; }
  .square .tagline { right: 26px; top: 218px; font-size: 28px; font-weight: 300;
    text-align: right; line-height: 36px; }
</style>
</head>
<body>
<div class="board">

  <section class="banner cover" aria-label="Cover photo">
    <div class="band-top"></div>
    <div class="band-mid"></div>
    <div class="band-bottom"></div>
    <div class="portrait" role="img" aria-label="Photo of Dr. Velmora in a white lab coat, arms crossed"></div>
    <div class="kicker"><span class="rule"></span>THE ALL NEW<span class="rule"></span></div>
    <div class="show-name"><span class="dot"></span>Dr. Velmora Hour</div>
    <p class="tagline">airing weekly in over 100 new markets in the US!</p>
  </section>
  <p class="caption" style="left:66px;top:596px;">Facebook Cover Photo</p>

  <section class="banner feed" aria-label="Feed post">
    <div class="band-top"></div>
    <div class="band-mid"></div>
    <div class="band-bottom"></div>
    <div class="portrait" role="img" aria-label="Photo of Dr. Velmora in a white lab coat, arms crossed"></div>
    <div class="kicker"><span class="rule"></span>THE ALL NEW<span class="rule"></span></div>
    <div class="show-name"><span class="dot"></span>Dr. Velmora Hour</div>
    <p class="tagline">airing weekly in over 100 new markets in the US!</p>
    <div class="cta">Click here to learn where YOU can watch!</div>
  </section>
  <p class="caption" style="left:66px;top:1044px;">FB</p>

  <section class="banner square" aria-label="Square post">
    <div class="band-top"></div>
    <div class="band-mid"></div>
    <div class="band-bottom"></div>
    <div class="portrait" role="img" aria-label="Photo of Dr. Velmora in a white lab coat, arms crossed"></div>
    <div class="kicker"><span class="rule"></span>THE ALL NEW<span class="rule"></span></div>
    <div class="show-name"><span class="dot"></span>Dr. Velmora Hour</div>
    <p class="tagline">airing weekly in<br>over 100 new<br>markets in the US!</p>
  </section>
  <p class="caption" style="left:777px;top:1044px;">Instagram</p>

</div>
</body>
</html>
```